Looking for a modern, Professional business card design

We have a simple business card, but are looking for a more modern, professional look. A sample of the basic card is attached as well as the logo. We would also like to add that we offer:
Struggling with your finances?
- Learn to become debt free
- Discover the power of cash
- Control your money instead of it controlling you
Let us help you achieve a new level of financial freedom!
Also, we would like to have a "SPECIAL OFFER!: FREE 30 minute consultation"
Financial Planning

```html
<!DOCTYPE html>
<html lang="en">
<head>
<meta charset="utf-8">
<title>Brightledger Money Coaching – Business Card</title>
<link rel="stylesheet" href="https://fonts.googleapis.com/css2?family=Roboto:ital,wght@0,400;0,500;0,700;0,900;1,700&display=swap">
<style>
  :root {
    --backdrop: #9b9b9b;
    --paper: #eeeff1;
    --green: #2a8f3c;
    --green-deep: #1f7a30;
    --green-light: #8dc63f;
    --ink: #1a1a1a;
    --white: #ffffff;
  }
  * { margin: 0; padding: 0; box-sizing: border-box; }
  html, body {
    width: 1105px; height: 1200px; overflow: hidden;
    background: var(--backdrop);
    font-family: "Roboto", Arial, sans-serif;
  }
  .card {
    position: absolute; left: 184px;
    width: 744px; height: 425px; overflow: hidden;
  }
  .card--front { top: 120px; background: var(--paper); }
  .card--back {
    top: 636px;
    background: radial-gradient(ellipse at 50% 40%, #8fc33c 0%, #55a53a 38%, var(--green-deep) 100%);
    color: var(--white); text-align: center;
  }
  .front-band { position: absolute; inset: 0; }
  .brand {
    position: absolute; left: 150px; top: 56px;
    display: flex; align-items: center; gap: 20px;
  }
  .brand__dot {
    width: 56px; height: 56px; border-radius: 50%;
    background: var(--green-light); flex: none;
  }
  .brand__text { display: flex; flex-direction: column; }
  .brand__name {
    font-weight: 900; font-size: 40px; color: var(--ink);
    letter-spacing: 0.5px; text-transform: uppercase; line-height: 44px;
    white-space: nowrap;
  }
  .brand__tagline {
    margin-top: 8px;
    font-size: 14px; color: #333; letter-spacing: 0.3px; white-space: nowrap;
  }
  .person {
    position: absolute; right: 438px; top: 320px; text-align: right; color: var(--white);
  }
  .person__name { font-weight: 700; font-size: 26px; line-height: 1.2; }
  .person__title { font-weight: 500; font-size: 19px; margin-top: 4px; }
  .contacts {
    position: absolute; left: 340px; top: 308px; list-style: none; color: var(--white);
    font-size: 20px;
  }
  .contacts li { display: flex; align-items: center; gap: 14px; height: 29.5px; white-space: nowrap; }
  .contacts svg { width: 18px; height: 18px; flex: none; }
  .offer-badge { position: absolute; left: 292px; top: 58px; width: 144px; height: 144px; }
  .divider {
    position: absolute; left: 90px; right: 90px; height: 2px;
    background: linear-gradient(90deg, transparent, rgba(255,255,255,0.75), transparent);
  }
  .divider--top { top: 218px; }
  .divider--bottom { top: 337px; }
  .pitch { position: absolute; left: 0; right: 0; top: 234px; }
  .pitch__headline { font-size: 22px; font-weight: 500; letter-spacing: 0.4px; text-transform: uppercase; }
  .pitch__points { font-size: 19px; line-height: 27px; margin-top: 5px; }
  .closing {
    position: absolute; left: 0; right: 0; top: 352px;
    font-size: 19px; font-weight: 700; font-style: italic;
  }
</style>
</head>
<body>
  <section class="card card--front">
    <svg class="front-band" viewBox="0 0 744 425" aria-hidden="true">
      <path d="M0,218 Q360,282 744,226 L744,236 Q360,290 0,234 Z" fill="#111"/>
      <path d="M0,232 Q370,296 744,230 L744,425 L0,425 Z" fill="var(--green)"/>
      <path d="M120,244 Q420,294 744,232" fill="none" stroke="var(--green-light)" stroke-width="2" opacity="0.8"/>
    </svg>
    <div class="brand">
      <span class="brand__dot"></span>
      <div class="brand__text">
        <span class="brand__name">Brightledger<br>Money Coaching</span>
        <p class="brand__tagline">Achieve a new level of personal freedom</p>
      </div>
    </div>
    <div class="person">
      <p class="person__name">Daniel R. Hayes</p>
      <p class="person__title">Personal Financial Coach</p>
    </div>
    <ul class="contacts">
      <li><svg viewBox="0 0 18 18"><rect x="4" y="1" width="10" height="16" rx="2" fill="none" stroke="#fff" stroke-width="1.6"/><circle cx="9" cy="14" r="1" fill="#fff"/></svg>(555) 014-2287</li>
      <li><svg viewBox="0 0 18 18"><rect x="1.5" y="4" width="15" height="10" fill="#fff"/><path d="M1.5,4 L9,10 L16.5,4" fill="none" stroke="var(--green)" stroke-width="1.3"/></svg>daniel@brightledgercoach.com</li>
      <li><svg viewBox="0 0 18 18"><circle cx="9" cy="9" r="7.5" fill="#fff"/><path d="M5,6 Q7,4 9,6 T8,10 Q6,12 7,15 M11,11 Q13,10 14,12" fill="none" stroke="var(--green)" stroke-width="1.4"/></svg>www.brightledgercoach.com</li>
    </ul>
  </section>

  <section class="card card--back">
    <svg class="offer-badge" viewBox="-72 -72 144 144" role="img" aria-label="Special offer: free 30 minute consultation">
      <defs>
        <path id="badge-ring" d="M-38,38 A53.7,53.7 0 1,1 38,38"/>
        <radialGradient id="badge-fill" cx="40%" cy="35%" r="70%">
          <stop offset="0" stop-color="#a5d24a"/>
          <stop offset="1" stop-color="#3f8f2c"/>
        </radialGradient>
      </defs>
      <text font-family="Roboto, Arial, sans-serif" font-weight="900" font-size="15" fill="#fff" letter-spacing="1">
        <textPath href="#badge-ring" textLength="245">FREE 30 MINUTE CONSULTATION</textPath>
      </text>
      <circle r="39" fill="url(#badge-fill)" stroke="#fff" stroke-width="3"/>
      <text y="-4" text-anchor="middle" font-family="Roboto, Arial, sans-serif" font-weight="900" font-size="14" fill="#fff">SPECIAL</text>
      <text y="14" text-anchor="middle" font-family="Roboto, Arial, sans-serif" font-weight="900" font-size="15" fill="#fff">OFFER!</text>
    </svg>
    <div class="divider divider--top"></div>
    <div class="pitch">
      <p class="pitch__headline">Struggling with your finances?</p>
      <p class="pitch__points">Learn to become debt free &bull; Discover the power of cash<br>Control your money instead of it controlling you</p>
    </div>
    <div class="divider divider--bottom"></div>
    <p class="closing">Let us help you achieve a new level of financial freedom!</p>
  </section>
</body>
</html>
```